Flyer for spiritual retreat (yoga, meditation, reiki, raw food)

I would like a flyer to promote my upcoming retreat and a matching Facebook banner.

The name of the retreat is "OutBloom the Spirit" and the tagline is "retreat into you"

The activities in the retreat include daily meditation, ecstatic dance, spiritual development workshops on intuition, energy healing etc and a reiki session is included.

I would like a flyer designed to promote this, something that is editable as I will be running this multiple times and will need to adjust the flyer to add the dates etc each time.

edit: add that here will be fully catered raw food and juices, and that the retreat price includes all accomodation, meals and workshops.

Please contact me if you need further info. Please also visit my website www.marlavosk.com and www.pagenest.com/koruhaven to see my current events and promotions.

Thank you,

Marla

Reason: Hi all, thank you all for your submissions. Apologies as I am traveling and do not have much access to internet and will review your submissions and provide feedback as soon as possible. Kind regards, Marla.

Target Market(s)

People who like meditation, yoga, fans of tomas brenner and wendell marsh, those interested in personal and spiritual development.

Industry/Entity Type

Health And Wellness

Requirements
Must have
• Please put the included reiki session as as added bonus. Something like "BONUS 30 minute reiki healing session" in a little star/banner/something that stands out.
• Please emphasise the "light" part of OutBloom as I am going for a play on words between in the light and enlightenment.
• Please include placeholder text for place, location, time
• Placeholder for price
• My name (see attached file - can change colour to suit) and website (www.marlavosk.com)
Nice to have
• I prefer rounded designs, curves rather than block designs.
Should not have
• Koru Haven logo

```html
<!DOCTYPE html>
<html lang="en">
<head>
<meta charset="utf-8">
<title>OutBloom the Spirit – Retreat Flyer</title>
<link rel="stylesheet" href="https://fonts.googleapis.com/css2?family=Sorts+Mill+Goudy:ital@0;1&family=Great+Vibes&family=Montserrat:wght@400&family=Tinos&display=swap">
<style>
  :root {
    --ink: #231f20;
    --gold: #d9b26a;
    --gold-deep: #b48a48;
    --gold-soft: #ecd3a0;
    --nebula: #8a6a1e;
    --bonus-yellow: #f7e41a;
    --white: #ffffff;
    --panel: #ffffff;
    --label: #2a2324;
  }
  html, body {
    margin: 0;
    padding: 0;
    overflow: hidden;
    background: var(--ink);
  }
  .flyer {
    position: relative;
    width: 848px;
    height: 1200px;
    overflow: hidden;
    background:
      radial-gradient(ellipse 380px 300px at 420px 300px, rgba(240,200,90,0.55), transparent 70%),
      radial-gradient(ellipse 520px 260px at 200px 280px, rgba(160,120,40,0.45), transparent 75%),
      radial-gradient(ellipse 300px 240px at 700px 500px, rgba(120,110,40,0.35), transparent 75%),
      linear-gradient(180deg, #2a2418 0%, #3b2f17 30%, #2b2418 55%, var(--ink) 72%);
  }
  .cosmic-art {
    position: absolute;
    left: 184px;
    top: 60px;
    width: 440px;
    height: 492px;
    border-radius: 50%;
    background: radial-gradient(ellipse at 50% 42%, rgba(255,240,190,0.75) 0%, rgba(230,180,80,0.45) 35%, rgba(160,110,40,0.15) 65%, transparent 80%);
  }
  .title {
    position: absolute;
    left: 0;
    top: 560px;
    width: 848px;
    height: 120px;
    margin: 0;
    font-weight: 400;
  }
  .title .plain {
    position: absolute;
    font-family: "Sorts Mill Goudy", "Georgia", serif;
    font-size: 66px;
    color: var(--white);
    top: 34px;
    line-height: 1;
  }
  .title .out { left: 62px; }
  .title .rest { left: 482px; }
  .title .bloom {
    position: absolute;
    left: 150px;
    top: -6px;
    font-family: "Great Vibes", cursive;
    font-size: 124px;
    line-height: 1;
    color: var(--gold);
    text-shadow: 0 2px 3px rgba(0,0,0,0.5);
  }
  .tagline {
    position: absolute;
    left: 294px;
    top: 672px;
    width: 494px;
    margin: 0;
    font-family: "Montserrat", sans-serif;
    font-size: 20px;
    letter-spacing: 13.4px;
    color: var(--white);
    white-space: nowrap;
  }
  .activities {
    position: absolute;
    left: 291px;
    top: 700px;
    width: 520px;
    margin: 0;
    font-family: "Tinos", "Times New Roman", serif;
    font-size: 19.5px;
    line-height: 31px;
    color: var(--gold-soft);
  }
  .bonus {
    position: absolute;
    left: 56px;
    top: 758px;
    width: 256px;
    height: 256px;
    border: 2px solid var(--gold);
    border-radius: 50%;
    text-align: center;
    font-family: "Sorts Mill Goudy", "Georgia", serif;
    color: var(--white);
  }
  .bonus .bonus-head {
    display: block;
    margin-top: 40px;
    font-size: 41px;
    color: var(--bonus-yellow);
    line-height: 1.1;
  }
  .bonus .bonus-body {
    display: block;
    font-size: 31px;
    line-height: 42px;
  }
  .details-panel {
    position: absolute;
    left: 0;
    top: 0;
  }
  .host-photo {
    position: absolute;
    left: 384px;
    top: 800px;
    width: 156px;
    height: 156px;
    border-radius: 50%;
    border: 5px solid var(--gold);
    background: radial-gradient(circle at 50% 40%, #8a7a5c 0%, #4d4a35 55%, #2f3a2a 100%);
  }
  .host-name {
    position: absolute;
    left: 560px;
    top: 850px;
    margin: 0;
    font-family: "Great Vibes", cursive;
    font-size: 54px;
    font-weight: 400;
    color: var(--gold-deep);
    line-height: 1;
  }
  .event-fields {
    position: absolute;
    left: 300px;
    top: 986px;
    width: 516px;
    margin: 0;
    padding: 0;
    list-style: none;
  }
  .event-fields li {
    display: flex;
    align-items: baseline;
    height: 50px;
  }
  .event-fields .label {
    width: 92px;
    text-align: right;
    padding-right: 18px;
    font-family: "Great Vibes", cursive;
    font-size: 30px;
    color: var(--label);
  }
  .event-fields .fill {
    flex: 1;
    border-bottom: 2px dotted var(--label);
    height: 18px;
  }
  .website {
    position: absolute;
    left: 42px;
    top: 1134px;
    margin: 0;
    font-family: "Sorts Mill Goudy", "Georgia", serif;
    font-style: italic;
    font-size: 25px;
    color: var(--white);
  }
</style>
</head>
<body>
<main class="flyer">
  <div class="cosmic-art" role="img" aria-label="Glowing golden star tetrahedron around a radiant meditating figure against a starry nebula"></div>

  <h1 class="title">
    <span class="plain out">Out</span>
    <span class="bloom">Bloom</span>
    <span class="plain rest">the Spirit</span>
  </h1>
  <p class="tagline">RETREAT INTO YOU</p>
  <p class="activities">The activities in the retreat include daily meditation, ecstatic dance, spiritual development workshops on intuition, energy healing etc</p>

  <div class="bonus">
    <span class="bonus-head">BONUS</span>
    <span class="bonus-body">30 minute<br>Reiki Healing<br>Session</span>
  </div>

  <svg class="details-panel" width="848" height="1200" viewBox="0 0 848 1200" aria-hidden="true">
    <path d="M848 822 L848 1200 L296 1200 C290 1060 330 960 420 900 C500 848 600 836 700 830 Q780 826 848 822 Z"
          fill="var(--panel)" stroke="var(--gold)" stroke-width="7"/>
  </svg>

  <div class="host-photo" role="img" aria-label="Portrait photo of retreat host Marla Vosk"></div>
  <h2 class="host-name">Marla Vosk</h2>

  <ul class="event-fields">
    <li><span class="label">Place</span><span class="fill"></span></li>
    <li><span class="label">Location</span><span class="fill"></span></li>
    <li><span class="label">Time</span><span class="fill"></span></li>
    <li><span class="label">Price</span><span class="fill"></span></li>
  </ul>

  <p class="website">www.marlavosk.com</p>
</main>
</body>
</html>
```